Brandwyn Fuel Retro Website Design

Have a logo. Need a website design to go along with the logo design. Full Design Specs are here: https://files.plinverdocs.net/sheet/d/8QmRtZxWv3-41pk527LNB_XY4HaPcOdsuw2K-rb6/view

Target Market(s)

Independent Gas Station Owners

Number of Pages Required

1 page

Font styles to use
Sans Serif

Colors

Designer to choose colors to be used in the design.

```html
<!DOCTYPE html>
<html lang="en">
<head>
<meta charset="utf-8">
<title>Brandwyn Fuel</title>
<link rel="stylesheet" href="https://fonts.googleapis.com/css2?family=Roboto+Slab:wght@400;700&family=Lato:wght@400;700&display=swap">
<style>
:root{
  --red:#d9001b;
  --red-bar:#b80016;
  --charcoal:#333333;
  --ink:#222222;
  --text:#3a3a3a;
  --white:#ffffff;
  --slab:"Roboto Slab", Georgia, serif;
  --sans:"Lato", Arial, sans-serif;
}
*{box-sizing:border-box;margin:0;padding:0}
html,body{width:1200px;height:2694px;overflow:hidden;background:var(--white)}
.page{position:relative;width:1200px;height:2694px;overflow:hidden;font-family:var(--sans);color:var(--text)}
.abs{position:absolute}

/* hero */
.hero-photo{position:absolute;left:0;top:0;width:1200px;height:718px;
  background:linear-gradient(100deg,#4d4f55 0%,#6a6c70 25%,#3b3f4a 55%,#1f2b4a 75%,#2a2d36 100%)}
.hero-shade{position:absolute;left:0;top:0;width:1200px;height:718px;background:linear-gradient(180deg,rgba(0,0,0,.55),rgba(0,0,0,.25) 40%,rgba(0,0,0,.35))}
.nav-rule{position:absolute;height:4px;border-top:1px solid #ccc;border-bottom:1px solid #ccc}
.nav{position:absolute;top:99px;display:flex;gap:30px;font-family:var(--slab);font-weight:700;font-size:16px;color:var(--white);white-space:nowrap}
.nav .active{color:var(--red)}
.brand-mark{position:absolute;border-radius:50%;background:var(--red)}
.brand-name{position:absolute;left:0;width:1200px;text-align:center;font-family:var(--slab);font-weight:700;color:var(--white);white-space:nowrap}
.hero-title{position:absolute;left:0;width:1200px;top:314px;text-align:center;font-family:var(--slab);font-weight:700;font-size:50px;color:var(--white);text-shadow:4px 4px 0 var(--red);white-space:nowrap}
.hero-sub{position:absolute;left:0;width:1200px;top:380px;text-align:center;font-family:var(--slab);font-weight:700;font-size:30px;color:var(--white)}
.btn{position:absolute;display:flex;align-items:center;justify-content:center;background:var(--red);color:var(--white);border-radius:30px;font-family:var(--slab);font-weight:700;font-size:17px}
.hero-arrow{position:absolute;top:346px;width:54px;height:54px;border-radius:50%;background:rgba(255,255,255,.55)}
.hero-arrow svg{position:absolute;left:17px;top:15px}

/* services */
.service-photo{position:absolute;top:616px;width:224px;height:224px;border-radius:50%;border:8px solid var(--white)}
.service-title{position:absolute;width:300px;text-align:center;font-family:var(--slab);font-weight:700;font-size:23px;color:var(--ink)}
.service-text{position:absolute;width:290px;text-align:center;font-size:15.5px;line-height:19.5px;color:#333}

/* about */
.about-title{position:absolute;left:0;width:1200px;top:1210px;text-align:center;font-family:var(--slab);font-weight:700;font-size:35px;color:var(--white)}
.about-text{position:absolute;left:225px;width:750px;top:1276px;text-align:center;font-size:18px;line-height:28px;color:#e8e8e8}
.btn-muted{background:#555}

/* projects */
.section-title{position:absolute;left:157px;top:1607px;font-family:var(--slab);font-weight:700;font-size:31px;color:var(--ink)}
.project-photo{position:absolute}
.project-title{position:absolute;font-family:var(--sans);font-weight:700;color:#333;text-transform:uppercase}
.project-text{position:absolute;font-size:13px;line-height:16px;color:#555}
.learn{position:absolute;font-weight:700;font-size:16.5px;color:var(--red)}
.divider{position:absolute;left:628px;width:416px;height:1px;background:#ccc}

/* footer */
.footer-head{position:absolute;top:2372px;font-family:var(--slab);font-weight:700;font-size:20px;color:var(--white)}
.footer-list{position:absolute;top:2412px;list-style:none;font-size:14.5px;line-height:27px;color:var(--white)}
.social{position:absolute;top:2415px;width:44px;height:44px;border-radius:50%;background:#4a4a4a}
.footer-bar{position:absolute;left:0;top:2621px;width:1200px;height:73px;background:var(--red-bar)}
.copyright{position:absolute;left:0;width:1200px;top:2643px;text-align:center;font-size:13.5px;color:#f0b3bb}
</style>
</head>
<body>
<div class="page">

  <!-- hero -->
  <div class="hero-photo" role="img" aria-label="Photo of white and blue fuel delivery trucks parked in a gravel yard"></div>
  <div class="hero-shade"></div>

  <div class="nav-rule" style="left:163px;width:316px;top:82px"></div>
  <div class="nav-rule" style="left:163px;width:316px;top:130px"></div>
  <div class="nav-rule" style="left:721px;width:317px;top:82px"></div>
  <div class="nav-rule" style="left:721px;width:317px;top:130px"></div>
  <nav class="nav" style="left:186px"><span class="active">HOME</span><span>ABOUT US</span><span>SERVICES</span></nav>
  <nav class="nav" style="left:735px;top:100px"><span>BLOGS</span><span>PROJECTS</span><span>CONTACT US</span></nav>

  <div class="brand-mark" style="left:582px;top:38px;width:36px;height:36px"></div>
  <div class="brand-name" style="top:94px;font-size:22px">BRANDWYN FUEL</div>

  <h1 class="hero-title">WELCOME TO BRANDWYN FUEL</h1>
  <p class="hero-sub">LOREM IPSUM DOLOR SIT AMET</p>
  <div class="btn" style="left:502px;top:437px;width:193px;height:62px;font-size:19px">LEARN MORE</div>

  <div class="hero-arrow" style="left:122px"><svg width="20" height="24" viewBox="0 0 20 24"><path d="M14 2 L5 12 L14 22" fill="none" stroke="#111" stroke-width="3"/></svg></div>
  <div class="hero-arrow" style="left:1039px"><svg width="20" height="24" viewBox="0 0 20 24"><path d="M6 2 L15 12 L6 22" fill="none" stroke="#111" stroke-width="3"/></svg></div>

  <!-- services -->
  <div class="service-photo" style="left:150px;background:radial-gradient(circle,#7b2a2a,#3a3a3a 60%,#222)" role="img" aria-label="Photo of a fuel pump meter on a delivery truck"></div>
  <div class="service-photo" style="left:478px;background:radial-gradient(circle,#b9bcc0,#8a8d91 60%,#5c5f63)" role="img" aria-label="Photo of a silver fuel tank trailer with hazard placard"></div>
  <div class="service-photo" style="left:830px;background:radial-gradient(circle,#f2f2f2,#d4d4d4 60%,#8d8d8d)" role="img" aria-label="Photo of a white farm fuel storage tank"></div>

  <svg class="abs" style="left:40px;top:856px" width="32" height="54" viewBox="0 0 32 54"><path d="M28 2 L4 27 L28 52" fill="none" stroke="#555" stroke-width="3"/></svg>
  <svg class="abs" style="left:1136px;top:856px" width="32" height="54" viewBox="0 0 32 54"><path d="M4 2 L28 27 L4 52" fill="none" stroke="#555" stroke-width="3"/></svg>

  <h3 class="service-title" style="left:108px;top:862px">FUEL DELIVERY</h3>
  <p class="service-text" style="left:113px;top:905px">Brandwyn Fuel provides fuel delivery for in-dependent gas stations, convenience stores, construction sites or any other commercial need.</p>
  <div class="btn" style="left:175px;top:1000px;width:166px;height:54px">LEARN MORE</div>

  <h3 class="service-title" style="left:441px;top:862px">OIL</h3>
  <p class="service-text" style="left:449px;top:905px">Looking for speciality auto, tractor, trac-tor trailer, aviation or other commercial oils and lubricants Brandwyn Fuel can help! Just call one of our customer</p>
  <div class="btn" style="left:511px;top:1000px;width:166px;height:54px">LEARN MORE</div>

  <h3 class="service-title" style="left:799px;top:864px">FARM FUEL</h3>
  <p class="service-text" style="left:806px;top:907px">Looking for gasoline, diesel red diesel off road fuel or farm diesel? We can deliver straight to your farm! We can setup your farm tanks, take care of EPA</p>
  <div class="btn" style="left:869px;top:1002px;width:166px;height:54px">LEARN MORE</div>

  <!-- about band -->
  <svg class="abs" style="left:0;top:1100px" width="1200" height="480" viewBox="0 0 1200 480">
    <polygon points="0,78 600,10 1200,78 1200,400 600,470 0,400" fill="var(--red)"/>
    <polygon points="0,86 600,20 1200,86 1200,392 600,458 0,392" fill="var(--charcoal)"/>
  </svg>
  <h2 class="about-title">ABOUT BRANDWYN FUEL</h2>
  <p class="about-text">tristique vitae consequat nec porta vel lectus Nulla sit amet aliquam enim Proin dui lectus cursus eu mattis laoreet viverra sit amet quam Curabitur vel dolor ultrices ipsum dictum tris-tique Praesent vitae lacus Ut velit enim vestibulum non fermentum nec</p>
  <div class="btn btn-muted" style="left:515px;top:1392px;width:166px;height:54px">LEARN MORE</div>

  <!-- projects -->
  <h2 class="section-title">LATEST PROJECTS</h2>
  <div class="project-photo" style="left:158px;top:1682px;width:429px;height:242px;background:linear-gradient(180deg,#c9cdd2 0%,#9e8f78 30%,#55606a 60%,#3a3f44 100%)" role="img" aria-label="Photo of a pickup truck parked at a fuel depot loading dock"></div>
  <h3 class="project-title" style="left:165px;top:1958px;width:420px;font-size:18.5px;line-height:26px">Mauris vel lacus vitae felis vestibulum volutpat etiam est nunc</h3>
  <p class="project-text" style="left:165px;top:2016px;width:380px;line-height:21.5px">tristique vitae consequat nec porta vel lectus Nulla sit amet diam Proin dui lectus cursus eu mattis laoreet viverra sit amet quam Curabitur vel dolor ultrices ipsum dictum tristique</p>
  <span class="learn" style="left:170px;top:2092px">Learn More</span>

  <div class="project-photo" style="left:628px;top:1682px;width:128px;height:118px;background:linear-gradient(135deg,#3b4a6b,#8a7f74 60%,#c9c2b8)" role="img" aria-label="Photo of a stockroom with supplies"></div>
  <h3 class="project-title" style="left:784px;top:1680px;width:270px;font-size:17.5px;line-height:23px">Mauris vel lacus vitae felis vestibulum volutpat</h3>
  <p class="project-text" style="left:784px;top:1732px;width:270px">Aristique vitae consequat nec porta vel lectus Nulla sit amet dui lectus cursus eu</p>
  <span class="learn" style="left:784px;top:1772px">Learn More</span>
  <div class="divider" style="top:1818px"></div>

  <div class="project-photo" style="left:630px;top:1842px;width:128px;height:118px;background:linear-gradient(135deg,#d8d6d0,#7f6e60 55%,#3e3e44)" role="img" aria-label="Photo of boxed oil products stacked on the floor"></div>
  <h3 class="project-title" style="left:786px;top:1837px;width:270px;font-size:17.5px;line-height:23px">Fusce tellus sed metus augue convallis et</h3>
  <p class="project-text" style="left:784px;top:1892px;width:270px">Aristique vitae consequat nec porta vel lectus Nulla sit amet dui lectus cursus eu</p>
  <span class="learn" style="left:786px;top:1929px">Learn More</span>
  <div class="divider" style="top:1981px"></div>

  <div class="project-photo" style="left:631px;top:2002px;width:128px;height:118px;background:linear-gradient(180deg,#3f4e7a,#6a4a52 50%,#2f3a5a)" role="img" aria-label="Photo of shelves stocked with oil and lubricant bottles"></div>
  <h3 class="project-title" style="left:787px;top:2000px;width:270px;font-size:17.5px;line-height:23px">Phasellus felis dolor scelerisque a tempus</h3>
  <p class="project-text" style="left:784px;top:2054px;width:270px">Aristique vitae consequat nec porta vel lectus Nulla sit amet dui lectus cursus eu</p>
  <span class="learn" style="left:787px;top:2093px">Learn More</span>

  <!-- footer -->
  <svg class="abs" style="left:0;top:2230px" width="1200" height="400" viewBox="0 0 1200 400">
    <polygon points="0,76 600,6 1200,76 1200,400 0,400" fill="#444"/>
    <polygon points="0,90 600,20 1200,90 1200,400 0,400" fill="var(--red)"/>
  </svg>
  <div class="brand-mark" style="left:586px;top:2262px;width:28px;height:28px;background:var(--white)"></div>
  <div class="brand-name" style="top:2298px;font-size:20px">BRANDWYN FUEL</div>

  <h4 class="footer-head" style="left:164px">COMPANY</h4>
  <ul class="footer-list" style="left:163px"><li>Home</li><li>About Us</li><li>Our Services</li><li>News</li><li>Contact Us</li></ul>
  <h4 class="footer-head" style="left:354px">RESOURCES</h4>
  <ul class="footer-list" style="left:354px;top:2410px"><li>Blogs</li><li>Projects</li><li>Support</li><li>Privacy Policy</li><li>Term of Use</li></ul>
  <h4 class="footer-head" style="left:574px">CONTACT US</h4>
  <ul class="footer-list" style="left:576px;top:2410px"><li>Brandwyn Fuel Company</li><li>(555) 214-6630</li><li>(555) 214-6631 (fax)</li><li>418 Harlow Mill Road,</li><li>Ashby, TX 75990</li></ul>
  <h4 class="footer-head" style="left:801px">FOLLOW US</h4>
  <div class="social" style="left:791px" aria-label="Social profile"></div>
  <div class="social" style="left:846px" aria-label="Social profile"></div>
  <div class="social" style="left:901px" aria-label="Social profile"></div>
  <div class="social" style="left:956px" aria-label="Social profile"></div>

  <div class="footer-bar"></div>
  <p class="copyright">© 2019 Company Name &nbsp;All right reserved</p>
</div>
</body>
</html>
```